CFO services graphic design

I own a business consulting firm called Thornfield Advisory and we need a graphic for CFO services in our colours and branding. The attached file "CFO services to be put into Thornfield advisory theme", shows the content for the design. The two other files show the theme and colours for the new design.

```html
<!DOCTYPE html>
<html lang="en">
<head>
<meta charset="utf-8">
<title>Thornfield Advisory — CFO Services</title>
<link rel="stylesheet" href="https://fonts.googleapis.com/css2?family=Inter:wght@400;700&family=Roboto:wght@700&display=swap">
<style>
  :root {
    --navy: #1e2a4a;
    --orange: #f29325;
    --blue: #009fe3;
    --paper: #ffffff;
  }
  html, body {
    margin: 0;
    padding: 0;
    width: 1200px;
    height: 1200px;
    overflow: hidden;
    background: var(--paper);
  }
  .cfo-diagram {
    display: block;
    width: 1200px;
    height: 1200px;
  }
  .service-frame .edge-outer {
    fill: none;
    stroke: var(--orange);
    stroke-width: 16;
    stroke-linejoin: round;
    stroke-linecap: round;
  }
  .service-frame .edge-inner {
    fill: none;
    stroke: var(--blue);
    stroke-width: 16;
    stroke-linejoin: round;
    stroke-linecap: butt;
  }
  .link-dash {
    stroke: var(--orange);
    stroke-width: 16;
  }
  .pointer line {
    stroke: var(--navy);
    stroke-width: 6;
  }
  .pointer polygon {
    fill: var(--navy);
  }
  .hub-ring { fill: var(--orange); }
  .hub-core { fill: var(--navy); }
  .hub-title {
    font-family: "Roboto", "Inter", sans-serif;
    font-weight: 700;
    font-size: 60px;
    fill: var(--paper);
    text-anchor: middle;
  }
  .service-label {
    font-family: "Inter", sans-serif;
    font-size: 34px;
    fill: var(--navy);
    text-anchor: middle;
  }
  .service-label .strong { font-weight: 700; }
  .service-label .plain { font-weight: 400; }
</style>
</head>
<body>
<svg class="cfo-diagram" viewBox="0 0 1932 1932" xmlns="http://www.w3.org/2000/svg" role="img" aria-label="Chief Financial Officer services diagram">
  <defs>
    <g id="service-frame" class="service-frame">
      <polyline class="edge-inner" points="-238,-671 -146,-394 146,-394 238,-671"/>
      <polyline class="edge-outer" points="-238,-671 0,-841 238,-671"/>
    </g>
    <line id="link-dash" class="link-dash" x1="-18" y1="-578" x2="18" y2="-578"/>
    <g id="pointer" class="pointer">
      <line x1="0" y1="-318" x2="0" y2="-350"/>
      <polygon points="0,-374 -14,-346 14,-346"/>
    </g>
  </defs>

  <g class="frames" transform="translate(966 966)">
    <use href="#service-frame"/>
    <use href="#service-frame" transform="rotate(45)"/>
    <use href="#service-frame" transform="rotate(90)"/>
    <use href="#service-frame" transform="rotate(135)"/>
    <use href="#service-frame" transform="rotate(180)"/>
    <use href="#service-frame" transform="rotate(225)"/>
    <use href="#service-frame" transform="rotate(270)"/>
    <use href="#service-frame" transform="rotate(315)"/>

    <use href="#link-dash" transform="rotate(22.5)"/>
    <use href="#link-dash" transform="rotate(67.5)"/>
    <use href="#link-dash" transform="rotate(112.5)"/>
    <use href="#link-dash" transform="rotate(157.5)"/>
    <use href="#link-dash" transform="rotate(202.5)"/>
    <use href="#link-dash" transform="rotate(247.5)"/>
    <use href="#link-dash" transform="rotate(292.5)"/>
    <use href="#link-dash" transform="rotate(337.5)"/>

    <use href="#pointer"/>
    <use href="#pointer" transform="rotate(45)"/>
    <use href="#pointer" transform="rotate(90)"/>
    <use href="#pointer" transform="rotate(135)"/>
    <use href="#pointer" transform="rotate(180)"/>
    <use href="#pointer" transform="rotate(225)"/>
    <use href="#pointer" transform="rotate(270)"/>
    <use href="#pointer" transform="rotate(315)"/>
  </g>

  <g class="hub">
    <circle class="hub-ring" cx="966" cy="966" r="309"/>
    <circle class="hub-core" cx="966" cy="966" r="250"/>
    <text class="hub-title" x="966" y="968">CHIEF FINANCIAL</text>
    <text class="hub-title" x="966" y="1030">OFFICER</text>
  </g>

  <text class="service-label" x="966">
    <tspan class="strong" x="966" y="350">Cost Accounting</tspan>
    <tspan class="strong" x="966" y="391">&amp; Cost</tspan>
    <tspan class="strong" x="966" y="432">Management</tspan>
  </text>

  <text class="service-label">
    <tspan class="strong" x="1386" y="483">Capital</tspan>
    <tspan class="strong" x="1386" y="524">Structure</tspan>
    <tspan class="strong" x="1386" y="566">and the</tspan>
    <tspan class="strong" x="1386" y="607">Cost of Capital</tspan>
  </text>

  <text class="service-label">
    <tspan class="strong" x="1563" y="917">Long-term &amp;</tspan>
    <tspan class="strong" x="1563" y="958">short-term</tspan>
    <tspan class="strong" x="1563" y="999">investment</tspan>
    <tspan class="strong" x="1563" y="1040">decisions</tspan>
  </text>

  <text class="service-label">
    <tspan class="strong" x="1390" y="1383">Performance</tspan>
    <tspan class="strong" x="1390" y="1424">Evaluation</tspan>
  </text>

  <text class="service-label">
    <tspan class="strong" x="971" y="1536">Budeting &amp;</tspan>
    <tspan class="strong" x="971" y="1577">Strategic</tspan>
    <tspan class="strong" x="971" y="1618">Planning</tspan>
  </text>

  <text class="service-label">
    <tspan class="strong" x="543" y="1370">Risk</tspan>
    <tspan class="strong" x="543" y="1411">Management</tspan>
  </text>

  <text class="service-label">
    <tspan class="strong" x="368" y="936">Compliance :</tspan>
    <tspan class="plain" x="368" y="977">tax, legal</tspan>
    <tspan class="plain" x="368" y="1018">and regulatory</tspan>
  </text>

  <text class="service-label">
    <tspan class="strong" x="543" y="477">Communication :</tspan>
    <tspan class="plain" x="543" y="518">Board of Directors,</tspan>
    <tspan class="plain" x="543" y="559">creditors, owners,</tspan>
    <tspan class="plain" x="543" y="600">investors, credit</tspan>
    <tspan class="plain" x="543" y="642">rating agencies</tspan>
  </text>
</svg>
</body>
</html>
```